New Innovative Counselling and psychotherapy Service needs Business Card design

Keep it simple and professional. On one side, just company name and logo (perhaps in all blue) and maybe a tag line.

On other side (all white) my name and Qualifications in centre

Industry/Entity Type

Health And Wellness

Contact Information for Business Card

Dara Whelby
Counsellor & Psychotherapist
BSc (Psychol.), BA, Dip. (Couns. & Psych.), PG.Cert (CBT), FGTrK, ONRE

I will also require Mobile no, Email and web site address of which I'll pass on to final designer.

Font styles to use
Sans Serif

Requirements
Must have
• My Logo Only and please use the colours in logo that is in it.
Should not have
• Any other images

```html
<!DOCTYPE html>
<html lang="en">
<head>
<meta charset="utf-8">
<title>Meadowlane – Business Card</title>
<link href="https://fonts.googleapis.com/css2?family=Open+Sans:wght@300;400;600;700&display=swap" rel="stylesheet">
<style>
  :root {
    --green: #92c95a;
    --green-soft: #eaf4e0;
    --blue: #4aaee2;
    --blue-soft: #e9f4fb;
    --ink: #3a3a3a;
    --white: #ffffff;
    --stage: #ece8e1;
  }
  * { box-sizing: border-box; margin: 0; padding: 0; }
  html, body { width: 1200px; height: 902px; overflow: hidden; }
  body {
    background: var(--stage);
    font-family: "Open Sans", Arial, sans-serif;
    position: relative;
  }
  .card {
    position: absolute;
    width: 525px;
    height: 300px;
    overflow: hidden;
    border-radius: 3px;
    box-shadow: 0 8px 24px rgba(0,0,0,.18);
  }
  /* Front */
  .card-front { left: 70px; top: 110px; background: var(--green); }
  .front-decor { position: absolute; right: -120px; top: -150px; }
  .front-brand {
    position: absolute; left: 40px; bottom: 50px;
    display: flex; align-items: center; gap: 14px;
    color: var(--white);
  }
  .brand-dot {
    width: 36px; height: 36px; border-radius: 50%;
    background: var(--white);
  }
  .front-brand .brand-name { font-size: 30px; font-weight: 400; letter-spacing: .5px; }

  /* Back */
  .card-back { left: 605px; top: 490px; background: var(--white); }
  .back-decor { position: absolute; right: -60px; top: -90px; }
  .back-brand {
    position: absolute; left: 34px; top: 40px;
    display: flex; align-items: center; gap: 12px; color: var(--ink);
  }
  .back-brand .brand-dot { background: var(--blue); width: 32px; height: 32px; }
  .back-brand .brand-name { font-size: 28px; font-weight: 400; }
  .contact {
    position: absolute; right: 24px; top: 118px;
    list-style: none; font-size: 11px; color: var(--ink);
  }
  .contact li { display: flex; align-items: center; gap: 8px; margin-bottom: 7px; }
  .contact svg { flex: none; }
  .person { position: absolute; left: 34px; top: 168px; color: var(--ink); }
  .person-name { font-size: 22px; font-weight: 700; color: var(--blue); line-height: 1.1; }
  .person-role { font-size: 13px; font-weight: 600; margin-top: 3px; }
  .person-quals { font-size: 11px; font-weight: 400; line-height: 1.4; margin-top: 2px; }
  .back-band { position: absolute; left: 0; bottom: 0; width: 100%; height: 26px; }
</style>
</head>
<body>

<section class="card card-front" aria-label="Card front">
  <svg class="front-decor" width="380" height="380" viewBox="0 0 380 380" aria-hidden="true">
    <circle cx="190" cy="190" r="185" fill="var(--white)"/>
    <circle cx="190" cy="190" r="170" fill="var(--blue)"/>
  </svg>
  <div class="front-brand">
    <span class="brand-dot"></span>
    <span class="brand-name">Meadowlane</span>
  </div>
</section>

<section class="card card-back" aria-label="Card back">
  <svg class="back-decor" width="280" height="280" viewBox="0 0 280 280" aria-hidden="true">
    <circle cx="140" cy="140" r="135" fill="var(--blue-soft)"/>
  </svg>

  <div class="back-brand">
    <span class="brand-dot"></span>
    <span class="brand-name">Meadowlane</span>
  </div>

  <ul class="contact">
    <li>
      <svg width="16" height="16" viewBox="0 0 16 16" aria-hidden="true"><circle cx="8" cy="8" r="8" fill="var(--blue)"/><rect x="5.5" y="3.5" width="5" height="9" rx="1" fill="none" stroke="#fff" stroke-width="1.2"/></svg>
      000 0000 0000
    </li>
    <li>
      <svg width="16" height="16" viewBox="0 0 16 16" aria-hidden="true"><circle cx="8" cy="8" r="8" fill="var(--blue)"/><rect x="4" y="5" width="8" height="6" fill="none" stroke="#fff" stroke-width="1.1"/><path d="M4 5l4 3.5L12 5" fill="none" stroke="#fff" stroke-width="1.1"/></svg>
      hello@meadowlane-mail.com
    </li>
    <li>
      <svg width="16" height="16" viewBox="0 0 16 16" aria-hidden="true"><circle cx="8" cy="8" r="8" fill="var(--blue)"/><circle cx="8" cy="8" r="4.5" fill="none" stroke="#fff" stroke-width="1"/><path d="M3.5 8h9M8 3.5c-2 2.5-2 6.5 0 9M8 3.5c2 2.5 2 6.5 0 9" fill="none" stroke="#fff" stroke-width=".9"/></svg>
      meadowlane.com
    </li>
  </ul>

  <div class="person">
    <h1 class="person-name">Dara Whelby</h1>
    <p class="person-role">Counsellor &amp; Psychotherapist</p>
    <p class="person-quals">BSc (Psychol.), BA, Dip. (Couns. &amp; Psych.),<br>PG.Cert (CBT), FGTrK, ONRE</p>
  </div>

  <svg class="back-band" viewBox="0 0 525 26" preserveAspectRatio="none" aria-hidden="true">
    <rect x="0" y="0" width="420" height="26" fill="var(--green)"/>
    <rect x="420" y="0" width="6" height="26" fill="var(--white)"/>
    <rect x="426" y="0" width="99" height="26" fill="var(--blue)"/>
  </svg>
</section>

</body>
</html>
```